Web Design for a Biotech Consulting Firm

We need a web site design for a new business based in Philadelphia called Verantel Dx. This is a consulting firm that will serve medical diagnostics industry, which is part of the life science/healthcare industry focusing on developing and marketing products that help in early detection, monitoring or management of diseases. Our consulting firm will help medical diagnostic companies to overcome key challenges in designing, evaluating and marketing new products.Our company name is Verantel Dx. Verantel is Latin word for "something" Dx represents diagnostics. The idea behind the name is that we help companies to transform the original, early product ideas ("nothing") into "something"; which is a product with full clinical utility that will help to improve health and well-being.The web site should use the visual feel of the logo (attached), be modern, simple and clean looking and represent creativity, innovation, scientific thinking and progress.
Updates

Wix Design is acceptable

Industry/Entity Type

Biotechnology

Coding

Coded - Design and coding required

Number of Pages Required

1 page

Font styles to use
Sans Serif

Requirements
Must have
• simple, clean look couple of pages
Should not have
• a lot of pages

```html
<!DOCTYPE html>
<html lang="en">
<head>
<meta charset="utf-8">
<title>Verantel Dx — Biotech Consulting Firm</title>
<link href="https://fonts.googleapis.com/css2?family=Montserrat:ital,wght@0,400;0,500;0,600;0,700;0,800;1,400&display=swap" rel="stylesheet">
<style>
:root{
  --blue:#1f87f0;
  --blue-deep:#0b55b3;
  --ink:#1b1e23;
  --text:#4a4f57;
  --muted:#8a9099;
  --line:#d9dde3;
  --soft:#f3f4f6;
  --footer:#3b3e43;
  --footer-deep:#2d2f33;
  --white:#fff;
}
*{box-sizing:border-box;margin:0;padding:0}
html,body{width:1200px;height:3143px;overflow:hidden}
body{position:relative;font-family:'Montserrat',sans-serif;color:var(--text);background:var(--white)}
.abs{position:absolute}
.accent{color:var(--blue)}
svg{display:block}

/* header */
.site-header{position:absolute;left:0;top:0;width:1200px;height:106px;background:var(--white);border-bottom:1px solid #eceef1}
.brand{position:absolute;left:141px;top:38px;display:flex;align-items:center;gap:10px;font-size:22px;font-weight:500;color:var(--ink);white-space:nowrap}
.brand-mark{width:12px;height:12px;background:var(--blue);display:block}
.contact-top{position:absolute;top:14px;display:flex;align-items:center;gap:10px;color:var(--ink);white-space:nowrap}
.icon-sq{width:30px;height:30px;border:1.5px solid var(--blue);display:flex;align-items:center;justify-content:center}
.nav{position:absolute;top:72px;left:522px;display:flex;font-size:14px;color:var(--ink)}
.nav a{text-decoration:none;color:inherit;display:block;padding-bottom:14px;white-space:nowrap}
.nav a.active{color:var(--blue);border-bottom:2px solid var(--blue)}

/* hero */
.hero{position:absolute;left:0;top:106px;width:1200px;height:493px;background:linear-gradient(90deg,#f3f6fa 0%,#e4ecf5 35%,#b9cce2 60%,#8fa9c8 100%)}
.hero-box{position:absolute;left:141px;top:122px;width:356px;height:251px;border:2px solid var(--blue)}
.hero-title{position:absolute;left:161px;top:134px;font-size:40px;font-weight:800;line-height:50px;color:var(--ink);white-space:nowrap}
.hero-sub{position:absolute;left:165px;top:244px;font-size:14px;line-height:22px;color:var(--ink);width:390px}
.btn{display:inline-flex;align-items:center;gap:8px;background:var(--blue);color:var(--white);font-size:13px;text-transform:uppercase;padding:0 24px;height:40px;box-shadow:0 4px 8px rgba(0,0,0,.18)}
.dots{position:absolute;display:flex;gap:6px}
.dots i{width:8px;height:8px;border:1px solid var(--blue);display:block}
.dots i.on{background:var(--blue)}

/* headings */
.sec-title{position:absolute;left:0;width:1200px;text-align:center;font-size:32px;font-weight:500;color:var(--ink)}
.sec-title::after{content:"";display:block;width:44px;height:2px;background:var(--blue);margin:14px auto 0}

/* about */
.about-frame{position:absolute;left:141px;top:670px;width:438px;height:402px;border:2px solid var(--blue)}
.about-media{position:absolute;left:162px;top:691px;width:438px;height:360px;background:radial-gradient(circle at 75% 40%,#7fe6f2 0%,#2bb6dc 25%,#1a6fc9 60%,#4b2f9e 100%)}
.about-text{position:absolute;left:684px;top:684px;width:376px}
.about-text h2{font-size:32px;font-weight:500;color:var(--ink)}
.about-text h2::after{content:"";display:block;width:44px;height:2px;background:var(--blue);margin-top:12px}
.about-lead{margin-top:20px;font-size:15px;font-weight:600;color:var(--ink)}
.about-body{margin-top:8px;font-size:12px;line-height:19px}
.point{display:flex;gap:20px;margin-top:22px}
.point .ico{flex:0 0 52px;height:52px;border:1.5px solid var(--blue);display:flex;align-items:center;justify-content:center}
.point h3{font-size:15px;font-weight:500;color:var(--ink);margin-bottom:6px}
.point p{font-size:12px;line-height:17px}
.link-more{margin-top:30px;font-size:13px;color:var(--blue);display:flex;align-items:center;gap:6px}

/* services */
.services-band{position:absolute;left:0;top:1143px;width:1200px;height:305px;background:linear-gradient(120deg,#0a4fa8,#0d5cc2 50%,#0a4fa8)}
.services-band .sec-title{color:var(--white);top:65px}
.services-sub{position:absolute;left:0;top:132px;width:1200px;text-align:center;font-size:15px;font-weight:500;color:var(--white)}
.card{position:absolute;top:1323px;height:232px;background:var(--white);border:1.5px solid var(--blue);text-align:center;padding-top:32px}
.card svg{margin:0 auto}
.card h3{margin-top:22px;font-size:15px;font-weight:600;color:var(--ink);white-space:nowrap}
.card p{margin:8px auto 0;width:176px;font-size:12px;line-height:16px;color:var(--text)}
.card .plus{position:absolute;left:50%;bottom:-12px;margin-left:-11px;width:22px;height:22px;background:var(--white);border:1.5px solid var(--blue);color:var(--blue);font-size:18px;line-height:18px}
.card.is-active{background:var(--blue)}
.card.is-active h3,.card.is-active p{color:var(--white)}

/* why */
.why{position:absolute;left:0;top:1639px;width:1200px;height:502px;background:linear-gradient(180deg,#f1f2f4,#e8eaed)}
.why .sec-title{top:55px}
.why-core{position:absolute;left:494px;top:200px;width:212px;height:183px;background:var(--white);box-shadow:0 4px 18px rgba(0,0,0,.06);display:flex;align-items:center;justify-content:center}
.why-core .logo-name{font-size:28px;font-weight:500;color:var(--ink);white-space:nowrap}
.why-links{position:absolute;left:0;top:0}
.feat{position:absolute;width:70px;height:70px;border:1.5px solid var(--blue);background:var(--white);display:flex;align-items:center;justify-content:center}
.feat.is-filled{background:var(--blue)}
.feat-label{position:absolute;font-size:15px;color:var(--ink);white-space:nowrap}
.feat-label.left{text-align:right;width:200px}

/* reviews */
.reviews .sec-title{top:2200px}
.quote-mark{position:absolute;left:0;width:1200px;text-align:center;top:2280px;font-size:88px;font-weight:800;color:#9dc4f3;line-height:1}
.review-text{position:absolute;left:300px;top:2342px;width:600px;text-align:center;font-size:14px;line-height:22px;font-style:italic;color:var(--text)}
.review-name{position:absolute;left:0;top:2416px;width:1200px;text-align:center;font-size:15px;font-weight:500;color:var(--ink)}
.arrow-sq{position:absolute;width:30px;height:30px;border:1.5px solid var(--blue);display:flex;align-items:center;justify-content:center;background:var(--white)}

/* partners */
.partners{position:absolute;left:0;top:2540px;width:1200px;height:317px;background:var(--soft)}
.partners .sec-title{top:63px}
.partner{position:absolute;top:149px;width:169px;height:98px;background:var(--white);border:1px solid #e1e4e8;display:flex;align-items:center;justify-content:center;font-size:24px;font-weight:600;color:#5f646b}
.partner.first{color:var(--blue);box-shadow:0 2px 6px rgba(0,0,0,.08)}

/* footer */
.site-footer{position:absolute;left:0;top:2857px;width:1200px;height:242px;background:var(--footer);color:#e6e8eb}
.foot-col{position:absolute;top:58px}
.foot-col h4{font-size:15px;font-weight:500;color:var(--white);padding-bottom:9px;border-bottom:1px solid #55585e;white-space:nowrap}
.foot-list{list-style:none;margin-top:12px;font-size:11px}
.foot-list li{margin-bottom:12px;padding-left:10px;position:relative}
.foot-list li::before{content:"";position:absolute;left:0;top:5px;width:3px;height:3px;background:var(--muted)}
.foot-item{display:flex;gap:10px;font-size:12px;margin-top:12px;line-height:16px}
.foot-item small{font-size:10px;display:block}
.field{margin-top:16px;width:212px;height:31px;border:1px solid #6b6e74;font-size:11px;color:#a7abb1;padding:8px 10px}
.btn-sm{margin-top:10px;height:31px;width:106px;font-size:11px;padding:0;justify-content:center;box-shadow:none}
.foot-brand{position:absolute;left:860px;top:96px;width:199px;display:flex;justify-content:center;font-size:21px;font-weight:500;color:var(--white);white-space:nowrap}
.social{position:absolute;top:170px;left:901px;display:flex;gap:11px}
.social i{width:31px;height:31px;border:1.5px solid #d8dadd;display:block}
.social i.on{background:var(--blue);border-color:var(--blue)}
.copyright{position:absolute;left:0;top:3099px;width:1200px;height:44px;background:var(--footer-deep);color:#d8dadd;text-align:center;font-size:11px;line-height:44px}
</style>
</head>
<body>

<header class="site-header">
  <div class="brand"><span class="brand-mark"></span><span>Verantel <span class="accent">Dx</span></span></div>
  <div class="contact-top" style="left:727px;font-size:17px">
    <span class="icon-sq"><svg width="14" height="14" viewBox="0 0 24 24"><path d="M6.6 10.8a15 15 0 0 0 6.6 6.6l2.2-2.2a1 1 0 0 1 1-.25 11 11 0 0 0 3.6.6 1 1 0 0 1 1 1V20a1 1 0 0 1-1 1A17 17 0 0 1 3 4a1 1 0 0 1 1-1h3.5a1 1 0 0 1 1 1 11 11 0 0 0 .6 3.6 1 1 0 0 1-.25 1z" fill="#1f87f0"/></svg></span>
    555 014 2290
  </div>
  <div class="contact-top" style="left:896px;font-size:14px">
    <span class="icon-sq"><svg width="14" height="11" viewBox="0 0 14 11"><rect x="0" y="0" width="14" height="11" fill="#1f87f0"/><path d="M0 0l7 6 7-6" fill="none" stroke="#fff" stroke-width="1.4"/></svg></span>
    info@veranteldx.com
  </div>
  <nav class="nav">
    <a class="active" href="#" style="width:54px;text-align:center">Home</a>
    <a href="#" style="margin-left:44px">About Us</a>
    <a href="#" style="margin-left:61px">Services</a>
    <a href="#" style="margin-left:57px">Resources</a>
    <a href="#" style="margin-left:60px">Contact Us</a>
  </nav>
</header>

<section class="hero">
  <div role="img" aria-label="Scientists in lab coats and safety glasses working with test tubes in a laboratory" style="position:absolute;inset:0"></div>
  <div class="hero-box"></div>
  <h1 class="hero-title">BIOTECH<br>CONSULTING <span class="accent">FIRM</span></h1>
  <p class="hero-sub">We Serve Medical Diagnostics Industry, Which Is Part Of The Life Science/healthcare Industry.</p>
  <a class="btn abs" style="left:162px;top:311px">Read More <svg width="18" height="8" viewBox="0 0 18 8"><path d="M0 4h16M13 1l3 3-3 3" stroke="#fff" fill="none"/></svg></a>
  <div class="dots" style="left:574px;top:450px"><i class="on"></i><i></i><i></i><i></i></div>
</section>

<section class="about">
  <div class="about-frame"></div>
  <div class="about-media" role="img" aria-label="Digital illustration of a DNA helix beside a close-up eye with hexagon data graphics"></div>
  <div class="about-text">
    <h2>About <span class="accent">Us</span></h2>
    <p class="about-lead">Duis autem vel eum iriure dolor in hendrerit.</p>
    <p class="about-body">Lorem ipsum dolor sit amet, consectetuer adipiscing elit, sedmk diam nonummy nibh euismod tincidunt ut laoreet dolore magna aliquam erat volutpat. Suscipit lobortis nisl ut aliquip ex eamo kl commodo consequat.</p>
    <div class="point">
      <div class="ico"><svg width="26" height="26" viewBox="0 0 26 26" fill="none" stroke="#6b7078" stroke-width="1.4"><circle cx="13" cy="13" r="11"/><circle cx="13" cy="13" r="6.5"/><circle cx="13" cy="13" r="2"/><path d="M13 13l9-9M19 4h3v3"/></svg></div>
      <div><h3>Mission</h3><p>Accumsan et iusto odio dignissim qui blandit dollarl praesent luptatum zzril delenit augue.</p></div>
    </div>
    <div class="point">
      <div class="ico"><svg width="30" height="20" viewBox="0 0 30 20" fill="none" stroke="#6b7078" stroke-width="1.4"><path d="M1 10C6 3 11 1 15 1s9 2 14 9c-5 7-10 9-14 9S6 17 1 10z"/><circle cx="15" cy="10" r="5"/><circle cx="15" cy="10" r="2"/></svg></div>
      <div><h3>Vision</h3><p>Accumsan et iusto odio dignissim qui blandit dollarl praesent luptatum zzril delenit augue.</p></div>
    </div>
    <div class="link-more">READ MORE <svg width="18" height="8" viewBox="0 0 18 8"><path d="M0 4h16M13 1l3 3-3 3" stroke="#1f87f0" fill="none"/></svg></div>
  </div>
</section>

<section class="services">
  <div class="services-band">
    <h2 class="sec-title">Our Services</h2>
    <p class="services-sub">Lorem ipsum dolor sit amet, consectetuer adipiscing elit, sedmk diam nonummy nibh euismod.</p>
  </div>
  <article class="card is-active" style="left:141px;width:219px">
    <svg width="56" height="56" viewBox="0 0 56 56" fill="none" stroke="#fff" stroke-width="1.6"><path d="M23 2h10v17l14-8 5 9-14 8 14 8-5 9-14-8v17H23V37L9 45l-5-9 14-8-14-8 5-9 14 8z"/></svg>
    <h3>Designing</h3>
    <p>Lorem ipsum dolor sit amet, consectetuer adipiscing elit, sedmk diam nonummy.</p>
    <span class="plus">+</span>
  </article>
  <article class="card" style="left:378px;width:215px">
    <svg width="56" height="56" viewBox="0 0 56 56" fill="none" stroke="#1f87f0" stroke-width="1.6"><circle cx="28" cy="28" r="19"/><circle cx="28" cy="28" r="13"/><path d="M28 2v7M28 47v7M2 28h7M47 28h7M9 9l5 5M42 42l5 5M47 9l-5 5M14 42l-5 5"/><path d="M21 35v-5M26 35v-9M31 35v-7M36 35v-12"/></svg>
    <h3>Evaluating &amp; Marketing</h3>
    <p>Lorem ipsum dolor sit amet, consectetuer adipiscing elit, sedmk diam nonummy.</p>
    <span class="plus">+</span>
  </article>
  <article class="card" style="left:611px;width:215px">
    <svg width="56" height="56" viewBox="0 0 56 56" fill="none" stroke="#1f87f0" stroke-width="1.6"><circle cx="28" cy="28" r="22"/><circle cx="28" cy="28" r="15"/><path d="M28 2v10M28 44v10M2 28h10M44 28h10"/><path d="M21 27h4v9h-4zM25 35h8a2 2 0 0 0 2-2l1-5a2 2 0 0 0-2-2h-5l1-4a2 2 0 0 0-3-1l-2 4"/></svg>
    <h3>Early Detection</h3>
    <p>Lorem ipsum dolor sit amet, consectetuer adipiscing elit, sedmk diam nonummy.</p>
    <span class="plus">+</span>
  </article>
  <article class="card" style="left:844px;width:215px">
    <svg width="56" height="56" viewBox="0 0 56 56" fill="none" stroke="#1f87f0" stroke-width="1.6"><path d="M50 28A22 22 0 1 1 28 6"/><circle cx="28" cy="28" r="16"/><path d="M28 20v12M22 26h12M17 36h6l2-4 3 6 2-4h9"/><circle cx="44" cy="12" r="2"/></svg>
    <h3>Management Of Diseases</h3>
    <p>Lorem ipsum dolor sit amet, consectetuer adipiscing elit, sedmk diam nonummy.</p>
    <span class="plus">+</span>
  </article>
</section>

<section class="why">
  <h2 class="sec-title">Why Choose <span class="accent">Us?</span></h2>
  <svg class="why-links" width="1200" height="502" viewBox="0 0 1200 502" fill="none" stroke="#bfc7d2" stroke-width="1">
    <path d="M382 185h58l54 50M382 291h112M382 397h58l54-50M817 185h-58l-53 50M817 291H706M817 397h-58l-53-50"/>
  </svg>
  <div class="why-core">
    <div class="logo-name">Verantel <span class="accent">Dx</span></div>
  </div>

  <span class="feat-label left" style="left:98px;top:176px">Years Of Experience</span>
  <div class="feat is-filled" style="left:311px;top:150px"><svg width="36" height="40" viewBox="0 0 36 40" fill="none" stroke="#fff" stroke-width="1.5"><circle cx="18" cy="15" r="13"/><circle cx="18" cy="15" r="8"/><path d="M14 15l3 3 5-6M10 26l-4 12 5-3 3 4 3-10M26 26l4 12-5-3-3 4-3-10"/></svg></div>

  <span class="feat-label left" style="left:98px;top:282px">Proffesional Team</span>
  <div class="feat" style="left:311px;top:256px"><svg width="44" height="38" viewBox="0 0 44 38" fill="none" stroke="#555a62" stroke-width="1.4"><circle cx="22" cy="12" r="6"/><circle cx="9" cy="15" r="5"/><circle cx="35" cy="15" r="5"/><path d="M12 37c0-8 4-13 10-13s10 5 10 13M1 34c0-6 3-10 8-10 2 0 3 .5 4 1M43 34c0-6-3-10-8-10-2 0-3 .5-4 1"/></svg></div>

  <span class="feat-label left" style="left:98px;top:388px">Best Valuation</span>
  <div class="feat" style="left:311px;top:362px"><svg width="40" height="40" viewBox="0 0 40 40" fill="none" stroke="#555a62" stroke-width="1.4"><path d="M14 6h12l4 5-10 9-10-9zM10 11h20"/><path d="M5 22l15 7 15-7M5 22v10l15 7 15-7V22M20 29v10"/></svg></div>

  <div class="feat" style="left:817px;top:150px"><svg width="36" height="40" viewBox="0 0 36 40" fill="none" stroke="#555a62" stroke-width="1.4"><path d="M16 4l6 3-7 13-6-3zM11 18l-2 4M21 15a10 10 0 0 1 1 18M4 38h28M8 33h20"/></svg></div>
  <span class="feat-label" style="left:900px;top:176px">Innovative Research</span>

  <div class="feat" style="left:817px;top:256px"><svg width="42" height="42" viewBox="0 0 42 42" fill="none" stroke="#555a62" stroke-width="1.4"><circle cx="21" cy="21" r="19"/><circle cx="21" cy="21" r="15"/><path d="M21 10v11l7 5"/></svg></div>
  <span class="feat-label" style="left:900px;top:282px">On Time Solutions</span>

  <div class="feat" style="left:817px;top:362px"><svg width="40" height="42" viewBox="0 0 40 42" fill="none" stroke="#555a62" stroke-width="1.4"><circle cx="20" cy="14" r="8"/><path d="M10 15a10 10 0 0 1 20 0M10 14v5M30 14v5M30 19c0 3-3 4-8 4M4 41c0-9 6-14 16-14s16 5 16 14M14 34v7M26 34v7"/></svg></div>
  <span class="feat-label" style="left:900px;top:388px">Start-up Support</span>
</section>

<section class="reviews">
  <h2 class="sec-title">Customer <span class="accent">Reviews</span></h2>
  <div class="quote-mark">&ldquo;</div>
  <p class="review-text">"Lorem ipsum dolor sit amet, consectetuer adipiscing elit, sedmk diam nonummy nibh euismod tincidunt ut laoreet dolore magna aliquam erat volutpat. Suscipit lobortis nisl ut aliquip ex eamo kl commodo consequat."</p>
  <p class="review-name">-Mr. Arlen Pereira</p>
  <div class="dots" style="left:574px;top:2461px"><i class="on"></i><i></i><i></i><i></i></div>
  <div class="arrow-sq" style="left:141px;top:2372px"><svg width="10" height="16" viewBox="0 0 10 16"><path d="M9 1L2 8l7 7" fill="none" stroke="#8a9099" stroke-width="1.3"/></svg></div>
  <div class="arrow-sq" style="left:1028px;top:2372px"><svg width="10" height="16" viewBox="0 0 10 16"><path d="M1 1l7 7-7 7" fill="none" stroke="#1f87f0" stroke-width="1.3"/></svg></div>
</section>

<section class="partners">
  <h2 class="sec-title">Our <span class="accent">Parteners</span></h2>
  <div class="arrow-sq" style="left:71px;top:183px"><svg width="10" height="16" viewBox="0 0 10 16"><path d="M9 1L2 8l7 7" fill="none" stroke="#8a9099" stroke-width="1.3"/></svg></div>
  <div class="partner first" style="left:141px">Timberline</div>
  <div class="partner" style="left:329px">Quadrix</div>
  <div class="partner" style="left:516px">Glasshaus</div>
  <div class="partner" style="left:703px">Millworks</div>
  <div class="partner" style="left:890px">Broadleaf</div>
  <div class="arrow-sq" style="left:1098px;top:183px"><svg width="10" height="16" viewBox="0 0 10 16"><path d="M1 1l7 7-7 7" fill="none" stroke="#1f87f0" stroke-width="1.3"/></svg></div>
</section>

<footer class="site-footer">
  <div class="foot-col" style="left:141px;width:145px">
    <h4>Quick <span class="accent">Links</span></h4>
    <ul class="foot-list">
      <li>Home</li><li>About Us</li><li>Services</li><li>Resources</li><li>Contact Us</li>
    </ul>
  </div>
  <div class="foot-col" style="left:332px;width:235px">
    <h4>Contact <span class="accent">Detail</span></h4>
    <div class="foot-item"><svg width="12" height="16" viewBox="0 0 12 16" fill="none" stroke="#d8dadd"><path d="M6 15S1 9 1 6a5 5 0 0 1 10 0c0 3-5 9-5 9z"/><circle cx="6" cy="6" r="2"/></svg><div>Verantel Dx<small>48 Sample Lane, Fairmont,<br>PA-191 00</small></div></div>
    <div class="foot-item" style="margin-top:18px"><svg width="14" height="14" viewBox="0 0 24 24" fill="none" stroke="#d8dadd" stroke-width="1.6"><path d="M6.6 10.8a15 15 0 0 0 6.6 6.6l2.2-2.2 4.6 1.4V20A17 17 0 0 1 3 4h3.5l1.4 4.6z"/></svg>555 014 2290</div>
    <div class="foot-item" style="margin-top:18px;font-size:11px"><svg width="14" height="11" viewBox="0 0 14 11" fill="none" stroke="#d8dadd"><rect x=".5" y=".5" width="13" height="10"/><path d="M.5.5l6.5 5 6.5-5"/></svg>info@veranteldx.com</div>
  </div>
  <div class="foot-col" style="left:593px;width:212px">
    <h4>Newsletter <span class="accent">Signup</span></h4>
    <p style="font-size:11px;line-height:17px;margin-top:12px">Lorem ipsum dolor sit amet, consectetu adipiscing elit, sedmk nonummy.</p>
    <div class="field">Email</div>
    <div class="btn btn-sm">Submit <svg width="14" height="8" viewBox="0 0 18 8"><path d="M0 4h16M13 1l3 3-3 3" stroke="#fff" fill="none"/></svg></div>
  </div>
  <div class="foot-brand">Verantel Dx</div>
  <div class="social" aria-label="Social links">
    <i class="on" aria-label="Social network"></i><i aria-label="Social network"></i><i aria-label="Social network"></i><i aria-label="Social network"></i>
  </div>
</footer>
<div class="copyright">Copyright 2019 - Verantel Dx. All Rights Reserved.</div>

</body>
</html>
```